New Business Card Design Project LORVANTI-Italy

we are LORVANTI-Italy
our company in the market for 3 years we are luxury cosmetic company and its about time for a facelift :)
i will like to have elegant luxurious and unique business card
that will give the person that get it a unique, luxurious and elegant impression
I'm VERY OPEN FOR NEW IDEAS , even duo i add a few files of things that i see on line and i like them

i add my logo as well
my website is LORVANTI.COM
(if you would like to see the main style that we have)

Target Market(s)

adult that have money :)

Industry/Entity Type

Business

Contact Information for Business Card

Name - Dario Lorvanti
Position - CEO and CO Founder
address - 4817 E Halvern
telephone - 555-384-1926
email - dario@lorvanti.com
fax - 555-384-1926
website - LORVANTI.COM

Colors
000000
959595
fbee3e
ffffff

Requirements
Must have
• big logo in GOLD color
• elegant look
• impressive
Nice to have
• not must but maybe classy pattern background
• not must but maybe emblem
• maybe clear plastic business card
Should not have
• colors
• images

```html
<!DOCTYPE html>
<html lang="en">
<head>
<meta charset="utf-8">
<title>LORVANTI Italy – Business Card</title>
<link href="https://fonts.googleapis.com/css2?family=Cormorant+Garamond:wght@600;700&family=Lato:wght@400&display=swap" rel="stylesheet">
<style>
  :root {
    --stage: #000000;
    --card: #231f20;
    --gold: #d8b04c;
    --ink: #ffffff;
    --rule: #45403f;
    --serif: "Cormorant Garamond", "Times New Roman", serif;
    --sans: "Lato", "Helvetica Neue", Arial, sans-serif;
  }
  * { margin: 0; padding: 0; box-sizing: border-box; }
  html, body {
    width: 1200px; height: 900px; overflow: hidden;
    background: var(--stage);
  }
  .canvas { position: relative; width: 1200px; height: 900px; }

  .card {
    position: absolute; top: 275px;
    width: 477px; height: 294px;
    background: var(--card);
  }
  .card--front { left: 116px; border-radius: 0 62px 0 62px; }
  .card--back  { left: 622px; border-radius: 62px 0 62px 0; }

  .brand-name {
    position: absolute;
    font-family: var(--serif); font-weight: 600;
    color: var(--gold); letter-spacing: 1px; line-height: 1;
    white-space: nowrap;
  }
  .brand-country {
    position: absolute;
    font-family: var(--serif); font-weight: 600;
    color: var(--gold); letter-spacing: 1.5px; line-height: 1;
    text-align: center;
  }

  /* front */
  .card--front .brand-name { right: 33px; top: 64px; font-size: 44px; }
  .card--front .brand-country { left: 210px; width: 240px; top: 127px; font-size: 18px; }

  .holder-name {
    position: absolute; left: 36px; top: 176px;
    font-family: var(--serif); font-weight: 700;
    font-size: 19px; color: var(--gold); letter-spacing: .5px;
  }
  .holder-rule {
    position: absolute; left: 190px; top: 185px;
    width: 260px; height: 1px; background: var(--rule);
  }
  .holder-title, .holder-address {
    position: absolute; left: 36px;
    font-family: var(--sans); font-size: 13px; color: var(--ink);
  }
  .holder-title { top: 199px; }
  .holder-address { top: 244px; }

  .contact-list {
    position: absolute; right: 26px; top: 213px;
    list-style: none;
    font-family: var(--sans); font-size: 13px; color: var(--ink);
    text-align: right;
  }
  .contact-list li {
    display: flex; justify-content: flex-end; align-items: center;
    gap: 6px; height: 17.5px;
  }
  .contact-list svg { width: 11px; height: 11px; fill: var(--gold); }

  /* back */
  .brand-seal {
    position: absolute; left: 190px; top: 40px;
    width: 98px; height: 98px;
  }
  .card--back .brand-name {
    left: 0; width: 477px; text-align: center;
    top: 158px; font-size: 43px;
  }
  .card--back .brand-country { left: 118px; width: 240px; top: 216px; font-size: 17px; }
  .web-address {
    position: absolute; left: 0; width: 477px; top: 246px;
    text-align: center;
    font-family: var(--serif); font-weight: 600;
    font-size: 14px; color: var(--gold); letter-spacing: .5px;
  }
</style>
</head>
<body>
<main class="canvas">

  <section class="card card--front" aria-label="Business card front">
    <div class="brand-name">LORVANTI</div>
    <div class="brand-country">ITALY</div>

    <div class="holder-name">DARIO LORVANTI</div>
    <div class="holder-rule"></div>
    <div class="holder-title">CEO and CO Founder</div>
    <div class="holder-address">4817 E Halvern</div>

    <ul class="contact-list">
      <li>555-384-1926
        <svg viewBox="0 0 24 24" aria-hidden="true"><path d="M6.6 10.8a15.1 15.1 0 0 0 6.6 6.6l2.2-2.2a1 1 0 0 1 1-.25 11.4 11.4 0 0 0 3.6.57 1 1 0 0 1 1 1V20a1 1 0 0 1-1 1A17 17 0 0 1 3 4a1 1 0 0 1 1-1h3.5a1 1 0 0 1 1 1c0 1.25.2 2.45.57 3.57a1 1 0 0 1-.25 1z"/></svg>
      </li>
      <li>555-384-1926
        <svg viewBox="0 0 24 24" aria-hidden="true"><path d="M6 2h9l3 3v5h1a3 3 0 0 1 3 3v7a2 2 0 0 1-2 2H4a2 2 0 0 1-2-2v-7a3 3 0 0 1 3-3h1zm2 2v6h8V6h-2V4zm9 9v2h2v-2zm-4 0v2h2v-2z"/></svg>
      </li>
      <li>dario@lorvanti.com
        <svg viewBox="0 0 24 24" aria-hidden="true"><path d="M2 5h20v14H2zm2 2v.5l8 5 8-5V7z"/></svg>
      </li>
    </ul>
  </section>

  <section class="card card--back" aria-label="Business card back">
    <svg class="brand-seal" viewBox="0 0 98 98" aria-hidden="true">
      <circle cx="49" cy="49" r="46" fill="none" stroke="var(--gold)" stroke-width="3"/>
    </svg>
    <div class="brand-name">LORVANTI</div>
    <div class="brand-country">ITALY</div>
    <div class="web-address">WWW.LORVANTI.COM</div>
  </section>

</main>
</body>
</html>
```